QRV Advisors needs a web site

We need a web site for www.qrvadvisors-example.com. QRV is a mergers and acquisition consulting company that focuses our buyer and seller services on logistics companies. We help put companies together, and help with legal and financial due diligence. We want the web site to express our service and show the logistics components. We want personalized images versus pictures of trucks and airplanes.

Our new logo uses Burgandy and grey colors. Image attached. We are not in to bold, big letters...classy, artistic, low key preferred. Confidentiality, experience, professional are what we want to express on the site.

All we expect for the first part of this project is a home page, and one subpage.  We are budgeting other funds for the technical aspects of the web site

Reason: All that I'm seeing so far is trucks, forklifts and planes. We are a legal mergers and acquisitions firm that focus on logistics. I like some of the images to say logistics, but really want it say legal, financial, and putting companies together. Will pay extra for the sub page if someone can impress us with a home page.

Reason: Swamped with another project at the moment...will work on this over the weekend and provide designer feedback and select final design by Tuesday

```html
<!DOCTYPE html>
<html lang="en">
<head>
<meta charset="utf-8">
<title>QRV Advisors</title>
<link href="https://fonts.googleapis.com/css2?family=Open+Sans:wght@400;600&display=swap" rel="stylesheet">
<style>
:root{
  --burgundy:#a50d3a;
  --burgundy-dark:#7e0a2c;
  --ink:#3a3a3a;
  --muted:#6b6b6b;
  --rule:#dcdcdc;
  --page:#f3f3f3;
  --band:#e6e6e6;
  --footer:#262626;
  --white:#ffffff;
}
*{box-sizing:border-box;margin:0;padding:0}
html,body{width:680px;height:1200px;overflow:hidden}
body{font-family:"Open Sans",Arial,sans-serif;background:var(--page);color:var(--ink);position:relative}
.abs{position:absolute}

/* hero */
.hero{left:0;top:0;width:680px;height:353px;background:linear-gradient(180deg,#e4e4e4 0%,#f1f1f1 40%,#ececec 100%);border-top:2px solid var(--burgundy)}
.hero-photo{left:280px;top:110px;width:400px;height:243px;background:linear-gradient(90deg,rgba(236,236,236,0) 0%,#c9cbcd 30%,#8d9399 55%,#d8d8d8 80%,#ececec 100%)}
.hero-copy{left:53px;top:150px;width:246px}
.hero-copy h1{font-weight:400;font-size:14px;letter-spacing:1.3px;color:#333;margin-bottom:5px}
.hero-copy p{font-size:8.1px;line-height:14.6px;color:#444}
.btn{display:flex;align-items:center;justify-content:center;gap:6px;font-size:8px;color:var(--white);height:24px;border-radius:1px}
.btn-read{left:53px;top:286px;width:89px;background:var(--burgundy)}
.btn-contact{left:149px;top:286px;width:89px;background:#2b2b2b}

/* header */
.brand{left:37px;top:36px;width:178px;height:78px;background:linear-gradient(180deg,#f7f7f7,#d9d9d9);clip-path:polygon(0 0,100% 0,78% 100%,0 100%);box-shadow:0 2px 4px rgba(0,0,0,.2);display:flex;align-items:center;gap:6px;padding-left:8px}
.brand-mark{width:10px;height:10px;background:var(--burgundy)}
.brand-name{font-size:15px;font-weight:600;color:#444;letter-spacing:1px}
.brand-sub{font-size:6.4px;line-height:7.5px;color:#555;border-left:1px solid #888;padding-left:4px;margin-left:2px}
.nav{left:190px;top:42px;width:458px;height:68px;background:linear-gradient(180deg,#b8103f,#950a33);clip-path:polygon(6% 0,100% 0,100% 100%,0 100%);display:flex;padding-left:26px}
.nav-item{flex:1;display:flex;flex-direction:column;align-items:center;justify-content:center;gap:6px;color:var(--white);font-size:8.4px;letter-spacing:.4px}
.nav-item.active{background:var(--burgundy-dark);flex:0 0 54px}

/* partners */
.partners{left:0;top:353px;width:680px;height:85px;background:var(--band);display:flex;align-items:center;justify-content:space-around;padding:0 30px}
.partner{font-size:12px;color:#6a6a6a;letter-spacing:.6px;display:flex;align-items:center;gap:5px}
.partner-dot{width:9px;height:9px;background:#6a6a6a}
.seal{width:44px;height:44px;border-radius:50%;background:#9a9a9a}

/* section heads */
.section-head{left:42px;width:596px;border-bottom:1px solid var(--rule);padding:0 7px 6px;font-size:12px;letter-spacing:.8px;color:#444;font-weight:400}
.section-head em{font-style:normal;color:var(--burgundy)}
.search{left:522px;top:456px;width:106px;border-bottom:2px solid #ccc;font-size:7px;color:#888;padding-bottom:4px;display:flex;justify-content:space-between;align-items:center}

/* services */
.arrow{width:26px;height:36px;background:var(--burgundy);top:537px;display:flex;align-items:center;justify-content:center}
.arrow-left{left:35px;border-radius:18px 0 0 18px}
.arrow-right{left:603px;border-radius:0 18px 18px 0}
.service{top:504px;width:102px;text-align:center}
.service-tile{width:102px;height:106px;background:linear-gradient(180deg,#f8f8f8,#e2e2e2);border-bottom:2px solid #aaa;box-shadow:0 1px 3px rgba(0,0,0,.15);display:flex;align-items:center;justify-content:center}
.service h3{font-weight:400;font-size:8.8px;color:var(--burgundy);margin-top:9px;line-height:10px;height:22px}
.service p{width:124px;margin-left:-11px;font-size:7.2px;line-height:10px;color:var(--muted);letter-spacing:.2px}
.pill{display:inline-block;margin-top:8px;background:var(--burgundy);color:var(--white);font-size:7px;padding:2px 8px;border-radius:8px;letter-spacing:.3px}

/* testimonials */
.dots{left:600px;top:760px;display:flex;gap:3px}
.dots i{width:6px;height:6px;border-radius:50%;background:#bbb}
.dots i:first-child{background:var(--burgundy)}
.testimonial{top:802px;width:250px;display:flex;gap:14px}
.portrait{flex:0 0 68px;height:62px;border:2px solid #ccc;background:linear-gradient(180deg,#dfe3e6,#7c8086)}
.quote{font-size:7.4px;line-height:12px;color:#555}
.quote b{font-weight:400;color:#aaa;font-size:12px;line-height:0}
.quote cite{display:block;font-style:normal;color:var(--burgundy);margin-top:3px}
.divider{left:328px;top:790px;width:1px;height:100px;background:var(--rule)}
.btn-all{left:273px;top:916px;width:112px;height:20px;background:var(--burgundy);color:var(--white);font-size:7.2px;letter-spacing:.5px;display:flex;align-items:center;justify-content:center;border-radius:1px}
.rule-end{left:42px;top:954px;width:596px;height:1px;background:var(--rule)}

/* newsletter */
.newsletter{left:0;top:970px;width:680px;height:50px;background:linear-gradient(180deg,#525252,#3a3a3a);display:flex;align-items:center;justify-content:center;gap:10px;color:var(--white)}
.newsletter span{font-size:10.5px;letter-spacing:.6px}
.field{background:var(--white);color:#999;font-size:7.6px;padding:0 7px;display:flex;align-items:center;height:20px;border-radius:1px}
.btn-sub{background:var(--burgundy);font-size:7px;padding:0 9px;height:20px;display:flex;align-items:center;margin-left:4px}

/* footer */
.footer{left:0;top:1020px;width:680px;height:154px;background:var(--footer);color:var(--white)}
.footer-col{top:27px}
.footer-col h4{font-weight:400;font-size:8.8px;letter-spacing:.6px;margin-bottom:14px}
.footer-col li{list-style:none;font-size:7.2px;line-height:9px;margin-bottom:8px;padding-left:2px;color:#e6e6e6}
.qm-field{position:absolute;height:17px;width:91px;font-size:7px}
.qm-msg{position:absolute;left:97px;top:0;width:92px;height:41px;align-items:flex-start;padding-top:4px}
.qm-send{position:absolute;left:97px;top:48px;width:92px;height:17px;background:var(--burgundy);font-size:7.6px;display:flex;align-items:center;justify-content:center}
.bottom-bar{left:0;top:1174px;width:680px;height:26px;background:var(--burgundy);color:var(--white);display:flex;align-items:center;justify-content:space-between;padding:0 42px 0 54px;font-size:7.2px}
.social{display:flex;gap:6px}
.social i{width:14px;height:14px;border-radius:50%;background:var(--white)}
</style>
</head>
<body>

<section class="hero abs">
  <div class="hero-photo abs" role="img" aria-label="Two businessmen shaking hands in a bright office"></div>
  <div class="hero-copy abs">
    <h1>QRV ADVISORS</h1>
    <p>Quarry Ridge Ventures, LLC assists logistics industry business owners in implementing corporate growth and exit strategies. This includes logistics merger and acquisition (M&amp;A) advisory services along with business development consulting. The firm's management team consists of industry executives with extensive experience and relationships in the logistics industry.</p>
  </div>
  <a class="btn btn-read abs">Read more <svg width="7" height="7" viewBox="0 0 7 7"><path d="M1 0 7 3.5 1 7Z" fill="#fff"/></svg></a>
  <a class="btn btn-contact abs">Contact us <svg width="9" height="6" viewBox="0 0 9 6"><rect width="9" height="6" fill="#fff"/></svg></a>
</section>

<header>
  <div class="brand abs">
    <i class="brand-mark"></i>
    <span class="brand-name">QRV</span>
    <span class="brand-sub">QUARRY<br>RIDGE<br>VENTURES</span>
  </div>
  <nav class="nav abs">
    <div class="nav-item active">
      <svg width="22" height="18" viewBox="0 0 22 18"><path d="M11 0 22 9h-3v9h-5v-6H8v6H3V9H0Z" fill="#fff"/></svg>HOME</div>
    <div class="nav-item">
      <svg width="26" height="18" viewBox="0 0 26 18"><circle cx="8" cy="4" r="4" fill="#fff"/><circle cx="18" cy="4" r="4" fill="#fff"/><path d="M1 18c0-6 3-9 7-9s7 3 7 9ZM11 18c0-6 3-9 7-9s7 3 7 9Z" fill="#fff"/></svg>ABOUT US</div>
    <div class="nav-item">
      <svg width="20" height="20" viewBox="0 0 20 20"><path d="M2 8h6V5a2 2 0 1 1 4 0v3h6v10H2Z" fill="#fff"/></svg>OUR SERVICES ▾</div>
    <div class="nav-item">
      <svg width="22" height="20" viewBox="0 0 22 20"><path d="M11 0 22 5 11 10 0 5Z" fill="#fff"/><path d="M0 10l11 5 11-5M0 14l11 5 11-5" stroke="#fff" stroke-width="1.6" fill="none"/></svg>CASE STUDIES</div>
    <div class="nav-item">
      <svg width="20" height="14" viewBox="0 0 20 14"><rect width="20" height="14" fill="#fff"/><path d="M0 0 10 8 20 0" stroke="#a50d3a" stroke-width="1.4" fill="none"/></svg>CONTACT US</div>
  </nav>
</header>

<section class="partners abs">
  <span class="partner"><i class="partner-dot"></i>HALLMERE</span>
  <span class="partner">BROOKVANE</span>
  <i class="seal" role="img" aria-label="Partner seal"></i>
  <span class="partner">OSTVELL</span>
  <span class="partner">KESTREL STANTON</span>
</section>

<h2 class="section-head abs" style="top:458px">OUR <em>SERVICES</em></h2>
<div class="search abs"><span>Search...</span><svg width="8" height="8" viewBox="0 0 8 8"><circle cx="5" cy="3" r="2.2" fill="none" stroke="#888" stroke-width="1"/><path d="M3.4 4.6 0.5 7.5" stroke="#888" stroke-width="1.2"/></svg></div>

<div class="arrow arrow-left abs"><svg width="8" height="10" viewBox="0 0 8 10"><path d="M8 0 0 5 8 10Z" fill="#fff"/></svg></div>
<div class="arrow arrow-right abs"><svg width="8" height="10" viewBox="0 0 8 10"><path d="M0 0 8 5 0 10Z" fill="#fff"/></svg></div>

<article class="service abs" style="left:52px">
  <div class="service-tile"><svg width="56" height="56" viewBox="0 0 56 56"><g fill="#555"><rect x="2" y="42" width="6" height="12"/><rect x="11" y="36" width="6" height="18"/><rect x="20" y="30" width="6" height="24"/><rect x="29" y="24" width="6" height="30"/><rect x="38" y="18" width="6" height="36"/></g><path d="M4 36C20 30 34 20 44 6" stroke="#a50d3a" stroke-width="5" fill="none"/><path d="M36 6 50 0 50 16Z" fill="#a50d3a"/></svg></div>
  <h3>Strategic Planning<br>&amp; Negotiation</h3>
  <p>Lorem dipsum dolora sitame adipscing elit. Morabi nisll digula astren esequat art.</p>
  <span class="pill">more details +</span>
</article>
<article class="service abs" style="left:204px">
  <div class="service-tile"><svg width="56" height="46" viewBox="0 0 56 46"><rect x="2" y="2" width="40" height="42" fill="none" stroke="#555" stroke-width="3"/><g stroke="#555" stroke-width="2.5"><path d="M9 12h26M9 19h26M9 26h18M9 33h14"/></g><path d="M30 36 50 10l5 4-20 26-7 2Z" fill="#a50d3a"/></svg></div>
  <h3>Legal Documentation</h3>
  <p>Lorem dipsum dolora sitame adipscing elit. Morabi nisll digula astren esequat art.</p>
  <span class="pill">more details +</span>
</article>
<article class="service abs" style="left:350px">
  <div class="service-tile"><svg width="56" height="46" viewBox="0 0 56 46"><rect x="20" y="10" width="34" height="28" fill="none" stroke="#555" stroke-width="3"/><g stroke="#555" stroke-width="2"><path d="M30 18h18M30 24h18M30 30h18"/></g><circle cx="18" cy="16" r="11" fill="#fff" stroke="#a50d3a" stroke-width="3.5"/><path d="M10 24 2 36" stroke="#a50d3a" stroke-width="5"/></svg></div>
  <h3>Due Diligence</h3>
  <p>Lorem dipsum dolora sitame adipscing elit. Morabi nisll digula astren esequat art.</p>
  <span class="pill">more details +</span>
</article>
<article class="service abs" style="left:501px">
  <div class="service-tile"><div role="img" aria-label="Group of business people icon" style="width:44px;height:46px;background:linear-gradient(90deg,#555 0 30%,#a50d3a 30% 70%,#555 70%);border-radius:4px"></div></div>
  <h3>Brokering</h3>
  <p>Lorem dipsum dolora sitame adipscing elit. Morabi nisll digula astren esequat art.</p>
  <span class="pill">more details +</span>
</article>

<h2 class="section-head abs" style="top:752px">CLIENT <em>TESTIMONIALS</em></h2>
<div class="dots abs"><i></i><i></i><i></i></div>

<figure class="testimonial abs" style="left:58px">
  <div class="portrait" role="img" aria-label="Portrait of a client in a suit"></div>
  <blockquote class="quote"><b>“</b> Lorem ipsum dolor sit amet, ectetur adipiscing elit. Phasellus tincidunt tellus leo, sodales vestibulum urna. hendrerit vel. Maecenas hasellus tincidunt ut pretium tortor vestibulum urna.<cite>- Daniel Reyes, Manager</cite></blockquote>
</figure>
<div class="divider abs"></div>
<figure class="testimonial abs" style="left:350px">
  <div class="portrait" role="img" aria-label="Portrait of a client in a suit"></div>
  <blockquote class="quote"><b>“</b> Lorem ipsum dolor sit amet, ectetur adipiscing elit. Phasellus tincidunt tellus leo, sodales vestibulum urna. hendrerit vel. Maecenas hasellus tincidunt ut pretium tortor vestibulum urna.<cite>- Peter Walsh, Supervisor</cite></blockquote>
</figure>

<a class="btn-all abs">VIEW ALL TESTIMONIALS</a>
<div class="rule-end abs"></div>

<section class="newsletter abs">
  <span>SUBSCRIBE TO OUR NEWSLETTER:</span>
  <div class="field" style="width:234px">Email Address</div>
  <div class="btn-sub">SUBSCRIBE</div>
</section>

<footer class="footer abs">
  <div class="footer-col abs" style="left:52px">
    <h4>ABOUT US</h4>
    <ul><li>Who we are</li><li>Client List</li><li>Case Studies</li><li>Contact Info</li></ul>
  </div>
  <div class="footer-col abs" style="left:153px">
    <h4>SERVICES OFFERED</h4>
    <ul><li>Strategic Planning<br>&amp; Negotiation</li><li>Legal Documentation</li><li>Due Diligence</li><li>Brokering</li></ul>
  </div>
  <div class="footer-col abs" style="left:294px">
    <h4>ADDITIONAL INFO</h4>
    <ul><li>Sitemap</li><li>FAQ</li><li>Privacy Policy</li><li>Terms &amp; Agreement</li></ul>
  </div>
  <div class="footer-col abs" style="left:427px">
    <h4>QUICK MESSAGE</h4>
    <div style="position:relative;width:190px;height:66px">
      <div class="field qm-field" style="top:0">Firstname</div>
      <div class="field qm-field" style="top:23px">Email Address</div>
      <div class="field qm-field" style="top:48px">Contact #</div>
      <div class="field qm-msg">Message</div>
      <div class="qm-send">Send Message</div>
    </div>
  </div>
</footer>

<div class="bottom-bar abs">
  <span>Quarry Ridge Ventures All Rights Reserved ® 2014</span>
  <div class="social" role="img" aria-label="Social media links"><i></i><i></i><i></i></div>
</div>

</body>
</html>
```